Coastline Premier Retreats Business Card Design

Design a business card for Coastline Premier Retreats. Look at the website for colors and reference. Card should have logo, name, title, office number, mobile number, email, URL and a tagline like, "Luxury Hotel & Resort Email Marketing" (This might change).

https://www.coastlinepremierretreats.example

The rest I will leave up to your imagination.

Contact Information for Business Card

Logo, name, title, office number, mobile number, email, URL and a tagline like, "Luxury Hotel & Resort Email Marketing" (This might change).

```html
<!DOCTYPE html>
<html lang="en">
<head>
<meta charset="UTF-8">
<title>Coastline Premier Retreats – Business Card</title>
<link href="https://fonts.googleapis.com/css2?family=Montserrat:wght@400;500;600;700&display=swap" rel="stylesheet">
<style>
  :root {
    --bg: #3a3a3c;
    --card-black: #1c1c1d;
    --card-black-top: #2a2a2b;
    --white: #ffffff;
    --orange: #f47a1f;
    --ink: #1e1e1e;
    --grey: #7a7a7a;
    --sea: #1fa7b5;
    --sea-deep: #11708a;
    --cliff: #4f6a3a;
    --sky: #5d86a8;
  }
  * { margin: 0; padding: 0; box-sizing: border-box; }
  html, body { width: 1200px; height: 987px; overflow: hidden; }
  body {
    background: var(--bg);
    font-family: "Montserrat", sans-serif;
    position: relative;
  }
  .card {
    position: absolute;
    width: 620px;
    height: 354px;
    border-radius: 4px;
    overflow: hidden;
    box-shadow: 0 14px 30px rgba(0,0,0,0.45);
  }
  /* Back of card */
  .card-back {
    left: 80px;
    top: 90px;
    background: radial-gradient(ellipse at 50% 20%, var(--card-black-top), var(--card-black) 70%);
    color: var(--white);
    display: flex;
    flex-direction: column;
    align-items: center;
    justify-content: center;
    gap: 34px;
  }
  .brand-name {
    display: flex;
    align-items: center;
    gap: 12px;
    font-weight: 700;
    text-transform: uppercase;
    letter-spacing: 0.06em;
    color: var(--white);
    white-space: nowrap;
  }
  .brand-name .mark {
    width: 12px;
    height: 12px;
    background: var(--orange);
    flex: none;
  }
  .card-back .brand-name { font-size: 30px; }
  .tagline {
    font-size: 15px;
    font-weight: 500;
    letter-spacing: 0.03em;
  }
  .tagline .amp { color: var(--orange); }
  /* Front of card */
  .card-front {
    left: 500px;
    top: 540px;
    background: var(--white);
  }
  .card-front .photo {
    position: absolute;
    inset: 0;
    width: 100%;
    height: 100%;
  }
  .card-front .brand-name {
    position: absolute;
    top: 44px;
    right: 28px;
    font-size: 17px;
    gap: 9px;
  }
  .card-front .brand-name .mark { width: 9px; height: 9px; }
  .person {
    position: absolute;
    left: 36px;
    top: 170px;
  }
  .person-name {
    font-size: 23px;
    font-weight: 700;
    color: var(--ink);
  }
  .person-title {
    font-size: 15px;
    color: var(--grey);
    margin-top: 2px;
  }
  .contact-list {
    list-style: none;
    margin-top: 18px;
    display: flex;
    flex-direction: column;
    gap: 5px;
  }
  .contact-list li {
    display: flex;
    align-items: center;
    gap: 9px;
    font-size: 14px;
    color: #555;
    white-space: nowrap;
  }
  .contact-list svg { width: 13px; height: 13px; flex: none; }
</style>
</head>
<body>

  <section class="card card-back">
    <div class="brand-name"><span class="mark"></span>Coastline Premier Retreats</div>
    <p class="tagline">Luxury Hotel <span class="amp">&amp;</span> Resort Email Marketing</p>
  </section>

  <section class="card card-front">
    <svg class="photo" viewBox="0 0 620 354" preserveAspectRatio="none" role="img" aria-label="Photograph of a rocky, tree-covered coastline above turquoise ocean surf">
      <defs>
        <linearGradient id="coastFill" x1="0" y1="0" x2="0" y2="1">
          <stop offset="0" stop-color="var(--sky)"/>
          <stop offset="0.3" stop-color="var(--cliff)"/>
          <stop offset="0.55" stop-color="var(--sea)"/>
          <stop offset="1" stop-color="var(--sea-deep)"/>
        </linearGradient>
      </defs>
      <polygon points="170,0 620,0 620,354 405,354" fill="url(#coastFill)"/>
    </svg>

    <div class="brand-name"><span class="mark"></span>Coastline Premier Retreats</div>

    <div class="person">
      <h1 class="person-name">Daniel Hayes</h1>
      <p class="person-title">President</p>
      <ul class="contact-list">
        <li>
          <svg viewBox="0 0 24 24"><path fill="var(--orange)" d="M6.6 10.8a15 15 0 0 0 6.6 6.6l2.2-2.2a1 1 0 0 1 1-.25 11.4 11.4 0 0 0 3.6.57 1 1 0 0 1 1 1V20a1 1 0 0 1-1 1A17 17 0 0 1 3 4a1 1 0 0 1 1-1h3.5a1 1 0 0 1 1 1c0 1.25.2 2.45.57 3.570a1 1 0 0 1-.25 1z"/></svg>
          012-555-0147
        </li>
        <li>
          <svg viewBox="0 0 24 24"><rect x="6" y="2" width="12" height="20" rx="2" fill="none" stroke="var(--orange)" stroke-width="2.4"/><circle cx="12" cy="18" r="1.3" fill="var(--orange)"/></svg>
          012-555-0148
        </li>
        <li>
          <svg viewBox="0 0 24 24"><rect x="2" y="5" width="20" height="14" fill="var(--orange)"/><path d="M2 5l10 8 10-8" fill="none" stroke="var(--white)" stroke-width="1.6"/></svg>
          info@coastlinepremierretreats.example
        </li>
        <li>
          <svg viewBox="0 0 24 24" fill="none" stroke="var(--orange)" stroke-width="2"><circle cx="12" cy="12" r="9.5"/><ellipse cx="12" cy="12" rx="4" ry="9.5"/><path d="M2.5 12h19M4 7h16M4 17h16"/></svg>
          coastlinepremierretreats.example
        </li>
      </ul>
    </div>
  </section>

</body>
</html>
```